Healthy Meal Delivery Website Needs to be updated, current, fresh and modern

Hi there,

The current website i have is super old and outdated.

I would like a beautiful modern site that has all the same content as the previous except with a a new, modern and trustworthy feel.

The current website is https://tovalplatefresh.com/

Target Market(s)

Health Conscious Young Professionals

Industry/Entity Type

Food Service

Font styles to use
Sans Serif

Requirements
Must have
• Modern Trustworthy feel
Should not have
• Anything out dated or cheesy or scammy

```html
<!DOCTYPE html>
<html lang="en">
<head>
<meta charset="utf-8">
<title>Toval Plate Fresh — Healthy Meal Delivery</title>
<link rel="stylesheet" href="https://fonts.googleapis.com/css2?family=Comic+Neue:wght@400;700&family=Open+Sans:wght@400;600;700&display=swap">
<style>
:root{
  --yellow:#f5ea14;
  --blue:#1e9bd7;
  --ink:#2b2b2b;
  --muted:#555;
  --light:#f4f4f4;
  --white:#fff;
  --footer:#2a2624;
  --wood:#5a3a22;
}
*{margin:0;padding:0;box-sizing:border-box}
html,body{width:1200px;height:2848px;overflow:hidden}
body{position:relative;font-family:"Open Sans",Arial,sans-serif;color:var(--ink);background:var(--white)}
.abs{position:absolute}
.head-font{font-family:"Comic Neue","Open Sans",sans-serif}

/* hero */
.hero{left:0;top:0;width:1200px;height:695px;overflow:hidden}
.hero-photo{position:absolute;inset:0;background:
  radial-gradient(ellipse 330px 330px at 1020px 390px,#e9e6e0 0,#dcd7cf 58%,rgba(0,0,0,0) 62%),
  radial-gradient(ellipse 220px 200px at 1050px 420px,#4e8a2a 0,#3d6e22 60%,rgba(0,0,0,0) 100%),
  linear-gradient(90deg,#3b2414 0%,#6b4528 35%,#553520 70%,#3a2415 100%)}
.topbar-line{left:0;top:76px;width:1200px;height:2px;background:rgba(255,255,255,.85)}
.social{left:122px;top:10px;display:flex;gap:20px}
.social span{width:12px;height:12px;border-radius:50%;background:var(--yellow);display:block}
.brand{left:122px;top:38px;display:flex;align-items:center;gap:10px}
.brand-mark{width:26px;height:26px;background:var(--yellow);border-radius:4px}
.brand-name{font-family:"Comic Neue",sans-serif;font-weight:700;font-size:20px;color:var(--white)}
.contact-top{top:42px;font-size:12px;color:var(--white);display:flex;align-items:center;gap:8px}
.contact-top svg{width:14px;height:14px;fill:var(--yellow)}
.auth{top:10px;display:flex;gap:10px;left:924px}
.pill{background:var(--yellow);color:#1b6fa8;font-size:11px;font-weight:600;padding:2px 12px;border-radius:4px}
.nav{top:90px;left:396px;display:flex;gap:19px;font-size:12px;color:var(--white)}
.nav a{color:inherit;text-decoration:none;padding-bottom:8px}
.nav a.active{color:var(--blue);border-bottom:2px solid var(--blue)}
.hero-title{left:120px;top:284px;font-family:"Comic Neue",sans-serif;font-weight:700;font-size:52px;color:var(--white)}
.hero-text{left:120px;top:346px;width:500px;font-size:12px;line-height:16px;color:var(--white)}
.btn{background:var(--yellow);color:#1b6fa8;font-family:"Comic Neue",sans-serif;font-weight:700;font-size:13px;text-align:center;border-radius:5px}
.hero-btn{left:122px;top:404px;width:134px;height:36px;line-height:36px}
.slide-nav{left:122px;top:640px;display:flex;gap:14px;color:var(--white);font-size:12px;align-items:center}
.mouse{left:591px;top:612px;width:18px;height:46px;border:2px solid var(--white);border-radius:10px}
.mouse::after{content:"";position:absolute;left:5px;top:8px;width:4px;height:12px;background:var(--white);border-radius:2px}

/* features */
.features{left:0;top:695px;width:1200px;height:581px;background:var(--light)}
.features-title{left:118px;top:60px;width:440px;font-family:"Comic Neue",sans-serif;font-size:30px;line-height:36px;color:var(--ink)}
.features-title em{font-style:normal;color:var(--blue)}
.features-text{left:118px;top:182px;width:450px;font-size:11px;line-height:15px;color:var(--muted)}
.veg{left:0;top:273px;width:545px;height:266px;border-radius:40% 45% 30% 35%;background:
  radial-gradient(circle at 40% 55%,#c8202a 0,#d8362a 30%,rgba(0,0,0,0) 55%),
  radial-gradient(circle at 70% 40%,#4d2a5e 0,rgba(0,0,0,0) 40%),
  radial-gradient(circle at 15% 60%,#e8d6b8 0,rgba(0,0,0,0) 35%),
  linear-gradient(90deg,#5d9b30,#e8742a,#c62a28,#7b3a80,#d7262b)}
.feature{width:210px;text-align:center}
.feature svg.ico{width:44px;height:44px;fill:var(--blue)}
.feature h3{font-size:11px;font-weight:400;letter-spacing:.5px;margin:6px 0 4px;color:var(--ink)}
.feature p{font-size:10.5px;line-height:14px;color:var(--muted)}
.circle-arrow{width:18px;height:18px}

/* menu */
.menu-head{left:0;top:1344px;width:1200px;text-align:center}
.menu-head h2{font-family:"Comic Neue",sans-serif;font-weight:400;font-size:29px;color:var(--ink)}
.menu-head p{width:660px;margin:12px auto 0;font-size:11px;line-height:15px;color:var(--muted)}
.tiles{left:0;top:1470px;width:1200px;height:243px;display:flex}
.tile{flex:1;position:relative}
.tile-label{position:absolute;left:0;right:0;text-align:center;color:var(--white)}
.tile-label strong{display:block;font-family:"Comic Neue",sans-serif;font-weight:700;font-size:27px}
.tile-label span{font-size:10px;line-height:12px;display:block}
.chev{top:1560px;width:30px;height:80px}
.view-all{left:530px;top:1762px;width:138px;height:36px;line-height:36px}

/* testimonials */
.testimonials{left:0;top:1846px;width:1200px;height:366px;background:var(--light)}
.testimonials h2{position:absolute;top:86px;width:100%;text-align:center;font-family:"Comic Neue",sans-serif;font-weight:400;font-size:29px}
.quote-mark{left:244px;top:140px;font-family:"Comic Neue",sans-serif;font-size:64px;color:var(--ink)}
.quote{left:290px;top:164px;width:630px;text-align:center;font-size:11px;line-height:16px;color:var(--muted)}
.quote-name{left:0;top:230px;width:1200px;text-align:center;font-size:16px}
.dots{left:572px;top:290px;display:flex;gap:7px}
.dots span{width:9px;height:9px;border-radius:50%;background:#333}
.dots span:first-child{background:var(--blue)}

/* newsletter */
.news-title{left:0;top:2264px;width:1200px;text-align:center;font-family:"Comic Neue",sans-serif;font-size:29px;line-height:35px}
.news-text{left:290px;top:2344px;width:620px;text-align:center;font-size:11px;line-height:15px;color:var(--muted)}
.email-input{left:317px;top:2435px;width:467px;height:38px;border:1px solid #ccc;border-radius:5px;padding-left:24px;line-height:36px;font-size:10px;color:#aaa;background:var(--white)}
.news-btn{left:790px;top:2433px;width:101px;height:42px;line-height:42px}

/* footer */
.footer{left:0;top:2546px;width:1200px;height:302px;background:
  radial-gradient(circle at 20% 30%,#3a3330,rgba(0,0,0,0) 40%),
  radial-gradient(circle at 80% 60%,#37302c,rgba(0,0,0,0) 40%),var(--footer);color:var(--white)}
.footer h4{font-family:"Comic Neue",sans-serif;font-weight:700;font-size:19px;color:var(--yellow);margin-bottom:18px}
.foot-col{top:50px;font-size:11px;line-height:18px}
.foot-col ul{list-style:none}
.foot-row{display:flex;align-items:center;gap:14px;margin-bottom:10px}
.foot-row svg{width:14px;height:14px;fill:var(--yellow)}
.foot-social{display:flex;gap:34px;margin:14px 0 20px 6px}
.foot-social span{width:12px;height:12px;border-radius:50%;background:var(--white);display:block}
.like-box{display:flex;gap:6px}
.like-box span{background:#4267b2;font-size:11px;padding:2px 10px;border-radius:3px}
.field{border:1px solid var(--white);height:22px;font-size:10px;padding-left:6px;line-height:20px}
.foot-line{left:125px;top:246px;width:955px;height:1px;background:rgba(255,255,255,.4)}
.copyright{left:125px;top:268px;font-size:11px}
.legal{left:890px;top:268px;font-size:11px}
</style>
</head>
<body>

<section class="abs hero">
  <div class="hero-photo" role="img" aria-label="Photo of a fresh salad with greens, tomatoes and pasta on a white plate over a dark wooden table"></div>
  <div class="abs social"><span></span><span></span><span></span><span></span></div>
  <div class="abs brand"><span class="brand-mark"></span><span class="brand-name">Toval Plate Fresh</span></div>
  <div class="abs contact-top" style="left:712px">
    <svg viewBox="0 0 24 24"><path d="M6.6 10.8a15 15 0 0 0 6.6 6.6l2.2-2.2c.3-.3.7-.4 1-.2 1.1.4 2.3.6 3.6.6.6 0 1 .4 1 1V20c0 .6-.4 1-1 1A17 17 0 0 1 3 4c0-.6.4-1 1-1h3.5c.6 0 1 .4 1 1 0 1.3.2 2.5.6 3.6.1.3 0 .7-.2 1z"/></svg>
    Phone : (416) 555-0182</div>
  <div class="abs contact-top" style="left:900px">
    <svg viewBox="0 0 24 24"><path d="M2 5h20v14H2zm2 2v.5l8 5 8-5V7z"/></svg>
    E-Mail : sales@tovalplatefresh.com</div>
  <div class="abs auth"><span class="pill">Login</span><span class="pill">Signup</span></div>
  <div class="abs topbar-line"></div>
  <nav class="abs nav">
    <a class="active">Home</a><a>Toval Meal Plans</a><a>Menu</a><a>Pricing</a><a>About</a><a>Press</a><a>Contact</a>
  </nav>
  <h1 class="abs hero-title">Fresh and so Delicious</h1>
  <p class="abs hero-text">Lorem Ipsum is simply dummy text of the printing and typesetting industry. Lorem Ipsum has been the industry's standard dummy text ever since the 1500s.</p>
  <div class="abs btn hero-btn">READ MORE</div>
  <div class="abs slide-nav">
    <svg width="20" height="14" viewBox="0 0 20 14"><path d="M8 1 2 7l6 6M2 7h17" stroke="#fff" stroke-width="2" fill="none"/></svg><span>Prev</span>
    <span>Next</span><svg width="20" height="14" viewBox="0 0 20 14"><path d="M12 1l6 6-6 6M18 7H1" stroke="#fff" stroke-width="2" fill="none"/></svg>
  </div>
  <div class="abs mouse"></div>
</section>

<section class="abs features">
  <h2 class="abs features-title">The TOVAL DIET <em>Delivers</em> Diet Meals To Your Door In Toronto, GTA &amp; Montreal</h2>
  <p class="abs features-text">Our fresh and delicious diet meals and snacks are made with only the best natural ingredients that nourish your body. Why not let us prepare your meals while you lose the weight?</p>
  <div class="abs veg" role="img" aria-label="Illustration of fresh vegetables: tomatoes, peppers, eggplant, carrots, onions and garlic"></div>

  <div class="abs feature" style="left:620px;top:60px">
    <svg class="ico" viewBox="0 0 24 24"><path d="M12 21 3.5 12.5A5 5 0 0 1 12 5.5a5 5 0 0 1 8.5 7z"/></svg>
    <h3>HEALTHY</h3>
    <p>The Toval Diet is a great way to ensure you are eating all the nutrients you need, and nothing your body doesn't need.</p>
    <svg class="circle-arrow" viewBox="0 0 20 20" style="margin-top:26px"><circle cx="10" cy="10" r="8" fill="none" stroke="#1e9bd7" stroke-width="1.5"/><path d="M7 10h6M10 7l3 3-3 3" stroke="#1e9bd7" stroke-width="1.5" fill="none"/></svg>
  </div>
  <div class="abs feature" style="left:848px;top:60px">
    <svg class="ico" viewBox="0 0 24 24"><path d="M3 4h14v2H5v13h13v-7h2v9H3z"/><path d="M7 11l4 4 10-11" stroke="#f5ea14" stroke-width="3" fill="none"/></svg>
    <h3>CHOICE</h3>
    <p>You can choose your own meals from over 100 tasty entrees, desserts and snack foods. You can choose your meals online, or we can select your meals for you.</p>
    <svg class="circle-arrow" viewBox="0 0 20 20" style="margin-top:10px"><circle cx="10" cy="10" r="8" fill="none" stroke="#1e9bd7" stroke-width="1.5"/><path d="M7 10h6M10 7l3 3-3 3" stroke="#1e9bd7" stroke-width="1.5" fill="none"/></svg>
  </div>
  <div class="abs feature" style="left:620px;top:320px">
    <svg class="ico" viewBox="0 0 24 24"><path d="M12 21 3.5 12.5A5 5 0 0 1 12 5.5a5 5 0 0 1 8.5 7z"/></svg>
    <h3>FRESH</h3>
    <p>All of our meals are real food, freshly prepared by our in-house expert chefs.</p>
    <svg class="circle-arrow" viewBox="0 0 20 20" style="margin-top:40px"><circle cx="10" cy="10" r="8" fill="none" stroke="#1e9bd7" stroke-width="1.5"/><path d="M7 10h6M10 7l3 3-3 3" stroke="#1e9bd7" stroke-width="1.5" fill="none"/></svg>
  </div>
  <div class="abs feature" style="left:848px;top:320px">
    <svg class="ico" viewBox="0 0 24 24"><circle cx="10" cy="10" r="5" fill="none" stroke="#1e9bd7" stroke-width="3" stroke-dasharray="3 2"/><circle cx="10" cy="10" r="2"/><circle cx="18" cy="17" r="3.5" fill="#f5ea14"/></svg>
    <h3>CUSTOMIZED</h3>
    <p>Your meals will be delivered fresh to your door, customized for your unique body type and level of activity.</p>
    <svg class="circle-arrow" viewBox="0 0 20 20" style="margin-top:26px"><circle cx="10" cy="10" r="8" fill="none" stroke="#1e9bd7" stroke-width="1.5"/><path d="M7 10h6M10 7l3 3-3 3" stroke="#1e9bd7" stroke-width="1.5" fill="none"/></svg>
  </div>
</section>

<header class="abs menu-head">
  <h2>Select From Over 100 Menu Items</h2>
  <p>You can choose your own meals from over 100 tasty entrees, desserts and snack foods. You can choose your meals online , or we can select your meals for you.</p>
</header>

<div class="abs tiles">
  <div class="tile" role="img" aria-label="Photo of a dinner plate: flat iron steak with roasted vegetables" style="background:linear-gradient(135deg,#3a2c24,#6a4a32 50%,#2d3a30)">
    <div class="tile-label" style="top:165px"><strong>Dinner</strong><span>Flat Iron Steak With<br>Rosted Vegitables</span></div>
  </div>
  <div class="tile" role="img" aria-label="Photo of breakfast: mushroom frittata with eggs" style="background:linear-gradient(135deg,#4a4038,#c9b89e 50%,#7a6650)">
    <div class="tile-label" style="top:165px"><strong>Breakfast</strong><span>Mushroom Frittata</span></div>
  </div>
  <div class="tile" role="img" aria-label="Photo of lunch: roasted beet walnut and goat cheese salad" style="background:linear-gradient(135deg,#6a8e3a,#c8d6a0 45%,#b84a3a 75%,#5e7a30)">
    <div class="tile-label" style="top:168px"><strong>Lunch</strong><span>Roasted Beet Walnut<br>&amp; Goat Cheese Salad</span></div>
  </div>
  <div class="tile" role="img" aria-label="Photo of a snack: fresh fruit with cottage cheese" style="background:linear-gradient(135deg,#8e6a3a,#c9a064 40%,#7a2a3a 80%,#3a2a3a)">
    <div class="tile-label" style="top:70px"><strong>Snack</strong><span>Fresh Fruit With Cottage<br>Cheese</span>
      <svg width="30" height="30" viewBox="0 0 30 30" style="margin-top:10px"><circle cx="12" cy="12" r="9" fill="none" stroke="#fff" stroke-width="2"/><path d="M19 19l8 8M8 12h8M12 8v8" stroke="#fff" stroke-width="2"/></svg>
    </div>
  </div>
</div>
<svg class="abs chev" style="left:40px" viewBox="0 0 30 80"><path d="M26 4 6 40l20 36" stroke="#f5ea14" stroke-width="5" fill="none"/></svg>
<svg class="abs chev" style="left:1130px" viewBox="0 0 30 80"><path d="M4 4l20 36L4 76" stroke="#1e9bd7" stroke-width="5" fill="none"/></svg>
<div class="abs btn view-all">VIEW ALL</div>

<section class="abs testimonials">
  <h2>What Clients Say`s</h2>
  <svg class="abs" style="left:42px;top:146px" width="32" height="80" viewBox="0 0 30 80"><path d="M26 4 6 40l20 36" stroke="#f5ea14" stroke-width="4" fill="none"/></svg>
  <svg class="abs" style="left:1134px;top:146px" width="32" height="80" viewBox="0 0 30 80"><path d="M4 4l20 36L4 76" stroke="#1e9bd7" stroke-width="4" fill="none"/></svg>
  <div class="abs quote-mark">“</div>
  <p class="abs quote">Ok, so you know I loved Toval food the first time but somehow, the second time I love it even more. My lentil soup was incredible! And I am looooving these huge snacks - melba, cheese, veggies, turkey pepperoni - I feel like I am able to graze all day log! So brilliant!</p>
  <div class="abs quote-name">Dana</div>
  <div class="abs dots"><span></span><span></span><span></span><span></span></div>
</section>

<h2 class="abs news-title">The TOVAL DIET Is Based On Real Foods Made With<br>Fresh And Natural Ingredients.</h2>
<p class="abs news-text">It's about eating the foods you love and emphasizing the ones that nourish your body; generous portions of fresh fruit, vegetables, meat, fish, nuts and seeds, with smaller servings of grains and dairy.</p>
<div class="abs email-input">E-Mail Address</div>
<div class="abs btn news-btn">Signup</div>

<footer class="abs footer">
  <div class="abs foot-col" style="left:125px">
    <h4>Quick Link</h4>
    <ul><li>Home</li><li>Toval Meal Plans</li><li>Menu</li><li>Pricing</li><li>About</li><li>Press</li><li>Contact</li></ul>
  </div>
  <div class="abs foot-col" style="left:348px">
    <h4>Stay In Touch</h4>
    <div class="foot-row"><svg viewBox="0 0 24 24"><path d="M6.6 10.8a15 15 0 0 0 6.6 6.6l2.2-2.2c.3-.3.7-.4 1-.2 1.1.4 2.3.6 3.6.6.6 0 1 .4 1 1V20c0 .6-.4 1-1 1A17 17 0 0 1 3 4c0-.6.4-1 1-1h3.5c.6 0 1 .4 1 1 0 1.3.2 2.5.6 3.6.1.3 0 .7-.2 1z"/></svg>416-555-0TPF (0182)</div>
    <div class="foot-row"><svg viewBox="0 0 24 24"><path d="M2 5h20v14H2zm2 2v.5l8 5 8-5V7z"/></svg>sales@tovalplatefresh.com</div>
    <div class="foot-social"><span></span><span></span><span></span></div>
    <div class="like-box"><span>Like 112K</span><span>Share</span></div>
  </div>
  <div class="abs foot-col" style="left:621px;width:200px">
    <h4>What Is Toval?</h4>
    <p style="font-size:10.5px;line-height:14px">Toval is the Toronto &amp; Montreal Diet Delivery program based on the Toval Diet™, healthy carbs and the right fats.<br>We provide you with 3 fresh meals, 2 snacks and a dessert delivered to your door before 6am.<br>Try our Toval Diet™ delivery plan and start Toval weight loss now!</p>
  </div>
  <div class="abs foot-col" style="left:877px;width:200px">
    <h4>Quick Contact</h4>
    <div style="display:flex;gap:8px"><div class="field" style="width:96px">Name</div><div class="field" style="width:96px">E-Mail</div></div>
    <div class="field" style="width:200px;height:68px;margin-top:6px">Massage</div>
    <div class="btn" style="width:98px;height:20px;line-height:20px;font-size:10px;margin-top:8px">SEND</div>
  </div>
  <div class="abs foot-line"></div>
  <div class="abs copyright">© Copyright 2018 Toval Plate Fresh - * Individual</div>
  <div class="abs legal">Privacy Policy - Terms &amp; conditions</div>
</footer>

</body>
</html>
```